WordPress Website for BidLinks Agency

We are in need of a complete WordPress design.

We will be seeking new clients and we want them to have a great idea of what our business does when they get to the page along with the products and services we offer. Our current website is www.mossyharbor.com and it really needs an upgrade. Wordpress would be great but our owner knows HTML as well so he can go in and edit things later if need be. Please apply if you can show what a Search Engine Marketing company does and can explain this information to a lay person. Also, the website should be responsive so it fits mobile, tablet, and desktop settings while changing to these different widths.

Also, we are not an SEO company, per se but an SEM / PPC company that operates on Zorvic BidLinks, Plim Promos, Chatterwall Promos, and other PPC platforms.

Themes are fine just as long as the content and the visuals display what a search engine marketing company does. Really looking for clients to know exactly why a search engine marketing company does when the get to the site, why they should use a search engine marketing company, and the best way to contact us to get a quote.

Here are some other search engine marketing sites that I like in terms of the content and the layout to give an idea of what should be included on the site:
http://www.fendowlabs.com/
http://www.k9rworks.com/
http://www.boulderpartners.com/
http://www.vjnpromo.com/
http://www.halvorteam.com/
http://meetthepinecrew.com/

Please include my new phone number of the website: 866-555-0142.

Thank you, 
Walt 

Target Market(s)

We are a search engine marketing company looking for more clients and want to be able to explain what a search engine marketing company does in layman's terms.

Industry/Entity Type

Marketing

Font styles to use
Sans Serif

Requirements
Must have
• About Us Page
Services Page
Home Page
Success Stories Page
Blog
Social Media links / feeds
Visuals of products / services offered
Jobs page
Nice to have
• Responsive design
Client Login / Space on the site for monthly client payments / Link to CoinTap or Rivermoss

```html
<!DOCTYPE html>
<html lang="en">
<head>
<meta charset="utf-8">
<title>Mossy Harbor Digital Marketing</title>
<link href="https://fonts.googleapis.com/css2?family=Ubuntu:wght@300;400;500;700&family=Open+Sans:wght@300;400;600&display=swap" rel="stylesheet">
<style>
:root{
  --red:#e31e24;
  --red-band:#e0262b;
  --ink:#333;
  --muted:#777;
  --soft:#f2f2f2;
  --line:#d8d8d8;
  --footer:#2b2b2b;
  --footer-text:#ddd;
  --white:#fff;
}
*{margin:0;padding:0;box-sizing:border-box}
html,body{width:718px;height:1200px;overflow:hidden;background:var(--white)}
body{position:relative;font-family:"Open Sans",sans-serif;color:var(--ink);font-size:10px}
.abs{position:absolute}

/* header */
.logo{left:40px;top:46px;display:flex;align-items:center;gap:6px}
.logo-dot{width:16px;height:16px;border-radius:50%;background:var(--red)}
.logo-name{font-family:"Ubuntu",sans-serif;font-weight:700;font-size:15px;color:var(--red);line-height:1.05}
.social{top:22px;left:587px;display:flex;gap:8px}
.social span{width:22px;height:22px;border-radius:50%;display:block}
.nav{top:57px;left:0;width:718px;font-size:11px}
.nav a{position:absolute;text-decoration:none;color:#666;white-space:nowrap}
.nav a.current{color:var(--red);font-weight:600}

/* hero */
.hero-band{left:0;top:262px;width:718px;height:238px;background:var(--soft)}
.hero{left:35px;top:86px;width:647px;height:230px;background:linear-gradient(90deg,#fafafa,#eeeeee);border:1px solid #ddd;box-shadow:0 8px 10px -8px rgba(0,0,0,.35)}
.hero-title{left:74px;top:150px;font-family:"Ubuntu",sans-serif;font-size:22px;font-weight:500;color:var(--ink);white-space:nowrap}
.hero-title em{font-style:normal;color:var(--red)}
.hero-sub{left:74px;top:183px;font-size:17px;font-weight:300;color:#555}
.btn{left:78px;top:218px;width:137px;height:28px;background:var(--red);color:var(--white);font-size:9.5px;display:flex;align-items:center;justify-content:center}
.dots{left:77px;top:260px;display:flex;gap:3px}
.dots span{width:10px;height:10px;border-radius:50%;background:#aaa}
.dots span:first-child{background:var(--red)}
.hero-art{left:432px;top:110px;width:176px;height:188px;border-radius:8px;background:linear-gradient(160deg,#d9e6c8 0%,#e6b46a 45%,#b9803a 100%)}

/* welcome */
.welcome{left:0;top:368px;width:718px;text-align:center}
.welcome h1{font-family:"Ubuntu",sans-serif;font-weight:300;font-size:22px;color:#444}
.welcome h1 strong{font-weight:500;color:var(--ink)}
.welcome h1 .accent{color:var(--red);font-weight:700}
.welcome .lead{font-size:12.5px;font-weight:300;color:#555;margin-top:5px}
.welcome .body{font-size:9.5px;font-weight:300;color:#666;width:620px;margin:2px auto 0;line-height:1.55}

/* products */
.products{left:0;top:500px;width:718px;height:246px;background:var(--red-band)}
.products h2{position:absolute;left:44px;top:32px;font-family:"Ubuntu",sans-serif;font-weight:400;font-size:20px;color:var(--white)}
.product{position:absolute;top:64px;width:155px;color:var(--white)}
.product .photo{width:152px;height:74px;border:3px solid var(--white)}
.product h3{font-family:"Ubuntu",sans-serif;font-weight:400;font-size:11px;margin-top:12px}
.product p{font-size:8.3px;line-height:1.55;margin-top:1px}

/* services */
.services-title{left:0;top:774px;width:718px;text-align:center;font-family:"Ubuntu",sans-serif;font-size:20px;color:#444;font-weight:300}
.services-title strong{font-weight:500;color:var(--ink)}
.service{position:absolute;top:809px;width:161px;text-align:center}
.service .badge{height:80px;border:1px solid var(--line);display:flex;align-items:center;justify-content:center;background:var(--white)}
.badge-plate{width:64px;height:52px;background:#eee;border-radius:3px}
.badge-circle{width:52px;height:52px;border-radius:50%;background:conic-gradient(#e33,#f90,#3a3,#39c,#96c,#e33)}
.service h3{font-family:"Ubuntu",sans-serif;font-weight:400;font-size:11px;margin-top:10px;color:var(--ink)}
.service p{font-size:8.3px;line-height:1.8;color:var(--muted);font-weight:300;margin-top:2px}

/* footer */
.footer{left:0;top:990px;width:718px;height:210px;background:var(--footer)}
.footer-heading{position:absolute;font-family:"Ubuntu",sans-serif;font-weight:400;font-size:9.5px;color:#eee;white-space:nowrap}
.tweet{position:absolute;left:76px;width:180px;padding-left:18px;font-size:8px;line-height:15px;color:#ccc}
.tweet svg{position:absolute;left:0;top:3px}
.tweet .handle{color:#c8191e}
.tweet-date{position:absolute;left:102px;font-size:8px;color:#c8191e}
.tweet-rule{position:absolute;left:76px;top:1100px;width:176px;border-top:1px solid #3c3c3c}
.footer-link{position:absolute;left:311px;font-size:7.5px;color:#ddd;white-space:nowrap}
.follow{position:absolute;left:310px;top:1150px;display:flex;gap:8px}
.follow span{width:19px;height:19px;display:block}
.newsletter-copy{position:absolute;left:460px;top:1008px;width:200px;font-family:"Ubuntu",sans-serif;font-size:9.5px;line-height:1.35;color:#eee}
.email{position:absolute;left:461px;top:1045px;width:181px;height:21px;background:var(--white);border-radius:2px;color:#777;font-size:8px;padding:5px 6px}
.subscribe{position:absolute;left:586px;top:1072px;width:56px;height:19px;background:var(--red);color:var(--white);font-size:8px;display:flex;align-items:center;justify-content:center}
.seal{position:absolute;top:1138px;height:36px;border-radius:3px}
</style>
</head>
<body>

<header>
  <div class="abs logo"><span class="logo-dot"></span><span class="logo-name">Mossy Harbor<br>Digital Marketing</span></div>
  <div class="abs social" aria-label="Social links">
    <span style="background:#55acee"></span><span style="background:#3b5998"></span><span style="background:#0e76a8"></span>
  </div>
  <nav class="abs nav">
    <a class="current" style="left:299px">Home</a>
    <a style="left:357px">About us</a>
    <a style="left:421px">Products</a>
    <a style="left:484px">Success stories</a>
    <a style="left:575px">Blog</a>
    <a style="left:618px">Contact us</a>
  </nav>
</header>

<div class="abs hero-band"></div>
<section class="abs hero"></section>
<h1 class="abs hero-title"><em>Mossy Harbor</em> Digital Marketing</h1>
<p class="abs hero-sub">Experts in Explosive Advertising</p>
<div class="abs btn">CONTACT US TO GET STARTED</div>
<div class="abs dots"><span></span><span></span><span></span><span></span></div>
<div class="abs hero-art" role="img" aria-label="Illustration of an open delivery box with marketing channel icons bursting out"></div>

<section class="abs welcome">
  <h1>Welcome to <span class="accent">Mossy Harbor</span> <strong>Digital Marketing..</strong></h1>
  <p class="lead">Phasellus felis dolor scelerisque a tempus eget lobortis id l</p>
  <p class="body">Praesent sit amet est. In dictum, dolor eu dictum porttitor, enim felis viverra mi, eget luctus massa purus quis odio. Etiam nulla massa, pharetra facili-sis, volutpat in, imperdiet sit amet, sem. Aliquam nec erat at purus cursus interdum. Vestibulum ligula augue, bibendum accumsan, vestibulum</p>
</section>

<section class="abs products">
  <h2>Our Products</h2>
  <div class="product" style="left:44px">
    <div class="photo" role="img" aria-label="Photo of a hand holding a glowing tablet with a globe" style="background:linear-gradient(135deg,#cfe3ef,#4a7f9c 60%,#243b4b)"></div>
    <h3>Product Tittle</h3>
    <p>Vivamus porttitor purus nisi eleifend libero tempus libero lectus feugiat felis Morbi diam mauris viverra.</p>
  </div>
  <div class="product" style="left:206px">
    <div class="photo" role="img" aria-label="Photo of hands reviewing a chart report" style="background:linear-gradient(135deg,#9cc3df,#3c6e98 60%,#1f3d5c)"></div>
    <h3>Product Tittle</h3>
    <p>Vivamus porttitor purus nisi eleifend libero tempus libero lectus feugiat felis Morbi diam mauris viverra.</p>
  </div>
  <div class="product" style="left:369px">
    <div class="photo" role="img" aria-label="Photo of a tablet showing a network of people" style="background:linear-gradient(135deg,#0f2a44,#1e6fa6 55%,#0a1c2e)"></div>
    <h3>Product Tittle</h3>
    <p>Vivamus porttitor purus nisi eleifend libero tempus libero lectus feugiat felis Morbi diam mauris viverra.</p>
  </div>
  <div class="product" style="left:531px">
    <div class="photo" role="img" aria-label="Photo of hands holding a tablet with a bar chart" style="background:linear-gradient(135deg,#f3f6f9,#cfdbe6 60%,#e9d8cf)"></div>
    <h3>Product Tittle</h3>
    <p>Vivamus porttitor purus nisi eleifend libero tempus libero lectus feugiat felis Morbi diam mauris viverra.</p>
  </div>
</section>

<h2 class="abs services-title"><strong>Services</strong> We Provide</h2>
<div class="service" style="left:77px">
  <div class="badge"><span class="badge-plate"></span></div>
  <h3>Zorvic BidLinks</h3>
  <p>Duis tincidunt lectus quis dui viverra ves-tibulum. Suspendisse vulputate aliquam dui. Nulla elementum dui ut augue.</p>
</div>
<div class="service" style="left:266px">
  <div class="badge"><span class="badge-plate"></span></div>
  <h3>Zorvic Metrics</h3>
  <p>Duis tincidunt lectus quis dui viverra ves-tibulum. Suspendisse vulputate aliquam dui. Nulla elementum dui ut augue.</p>
</div>
<div class="service" style="left:457px">
  <div class="badge"><span class="badge-circle" role="img" aria-label="Cluster of colourful social media icons"></span></div>
  <h3>Social Media Networking</h3>
  <p>Duis tincidunt lectus quis dui viverra ves-tibulum. Suspendisse vulputate aliquam dui. Nulla elementum dui ut augue.</p>
</div>

<footer class="abs footer"></footer>

<h4 class="footer-heading" style="left:76px;top:1009px">Latest Tweet</h4>
<p class="tweet" style="top:1032px">
  <svg width="12" height="10" viewBox="0 0 12 10"><path d="M1 2l4 3 6-4-2 6-5 2z" fill="#888"/></svg>
  <span class="handle">@harborwalt</span> Duis tincidunt lectus quis dui viverra vestibulum. Suspendisse vulputate aliquam dui. Nulla elementum dui ut
</p>
<span class="tweet-date" style="top:1083px">October 29, 2013</span>
<div class="tweet-rule"></div>
<p class="tweet" style="top:1106px">
  <svg width="12" height="10" viewBox="0 0 12 10"><path d="M1 2l4 3 6-4-2 6-5 2z" fill="#888"/></svg>
  <span class="handle">@harborwalt</span> Duis tincidunt lectus quis dui viverra vestibulum. Suspendisse vulputate aliquam dui. Nulla elementum dui ut
</p>
<span class="tweet-date" style="top:1157px">October 29, 2013</span>

<h4 class="footer-heading" style="left:310px;top:1009px">Terms &amp; Privacy</h4>
<span class="footer-link" style="top:1031px">Terms and Conditions</span>
<span class="footer-link" style="top:1047px">Privacy Statement</span>
<h4 class="footer-heading" style="left:310px;top:1069px">Teh Impact</h4>
<span class="footer-link" style="top:1087px">The Numbers</span>
<span class="footer-link" style="top:1103px">Annual Report</span>
<h4 class="footer-heading" style="left:310px;top:1130px">Follow Us on</h4>
<div class="follow" aria-label="Follow links">
  <span style="background:#3b5998"></span><span style="background:#1da1f2"></span><span style="background:#f26522"></span><span style="background:#d9252a"></span>
</div>

<p class="newsletter-copy">Stay in touch with us by signing up for our quarterly newsletters!</p>
<div class="email">email address</div>
<div class="subscribe">SUBSCRIBE</div>
<div class="seal" style="left:464px;width:54px;background:#777;border:2px solid #999"></div>
<div class="seal" style="left:549px;width:93px;background:#1d5e82"></div>

</body>
</html>
```